Cat-products company needs smart, yet endearing, business card

We need a business card design for a new, but up-and-running, business based in Honolulu, Hawaii. The business is Purrnest Nook Co. Our first product is the most environmentally-friendly cat grass kit ever seen on the planet. Future products, currently in the R&D phase, will include a variety of exciting cat scratchers. We also do consulting work to help apartment-dwellers make their home more cat-friendly and, in the future, plan on doing full, custom installs of structure to create high walkways for cats.

Target Market(s)

Middle-aged, apartment-dwelling, middle-class workers who own 1 or more cats and who dote on them.

Industry/Entity Type

Pet Care

Contact Information for Business Card

A striking, professional, yet warm and friendly design is what we're after.

Font styles to use
Serif
Sans Serif
Other font styles liked:
• Comfortaa

Colors

Designer to choose colors to be used in the design.

Requirements
Must have
• The company logo: (see attachment)
• The company name: Purrnest Nook Co
• The web address: www.purrnestnookco.com
• Email: support@purrnestnookco.com
• Phone: +1 (808) 571 6023
• Update (Fri Jun 30 3017 7:45pm Hawaii Time) I would like, is possible, uploaded picture of the cat grass kit on the back of the card with some text along the lines of: Purrnest Nook Co - Maker Of The Leafiest Feline Sprout Set Yet
Nice to have
• A cat picture, cartoon, real or silhouette that illustrates cats in action and/or relaxing; ie using the apartment space to live, play and relax in and being well-contented.
• Most of the website is done in the font: Comfortaa. It might be nice to continue using this for brand consistency.
Should not have
• Hard-to-read fonts.

```html
<!DOCTYPE html>
<html lang="en">
<head>
<meta charset="utf-8">
<title>Purrnest Nook Co – Business Card</title>
<link rel="stylesheet" href="https://fonts.googleapis.com/css2?family=Comfortaa:wght@700&family=Open+Sans:wght@400;700&display=swap">
<style>
  :root {
    --sun-yellow: #fdb515;
    --cocoa: #573530;
    --paper: #ffffff;
    --backdrop: #ece9e6;
  }
  * { margin: 0; padding: 0; box-sizing: border-box; }
  html, body { width: 1200px; height: 900px; overflow: hidden; }
  body {
    position: relative;
    background: var(--backdrop);
    font-family: "Open Sans", Arial, sans-serif;
  }

  /* Front side */
  .card-front {
    position: absolute;
    left: 78px; top: 34px;
    width: 587px; height: 364px;
    background: var(--sun-yellow);
    overflow: hidden;
    box-shadow: 0 6px 18px rgba(0,0,0,.18);
  }
  .card-front .panel { position: absolute; inset: 0; }
  .holder { position: absolute; left: 27px; top: 52px; color: var(--paper); }
  .holder-name { font-weight: 700; font-size: 21px; letter-spacing: .2px; line-height: 1.1; }
  .holder-title { font-size: 15px; margin-top: 3px; }
  .contact-list {
    position: absolute; left: 27px; top: 252px;
    list-style: none; color: var(--paper); font-size: 15px;
  }
  .contact-list li { display: flex; align-items: center; height: 21.5px; }
  .contact-list svg { width: 13px; height: 13px; margin-right: 7px; fill: var(--paper); }

  .front-mark {
    position: absolute; left: 290px; width: 280px; top: 125px;
    display: flex; flex-direction: column; align-items: center;
  }
  .front-mark-dot {
    width: 96px; height: 96px; border-radius: 50%;
    background: var(--sun-yellow);
  }
  .front-mark-name {
    margin-top: 24px;
    font-family: "Comfortaa", Arial, sans-serif;
    font-weight: 700; font-size: 25px;
    color: var(--sun-yellow); white-space: nowrap;
  }

  /* Back side */
  .card-back {
    position: absolute;
    left: 388px; top: 505px;
    width: 567px; height: 352px;
    background: var(--paper);
    box-shadow: 0 6px 18px rgba(0,0,0,.18);
    text-align: center;
  }
  .brand-square {
    position: absolute; left: 233px; top: 70px;
    width: 100px; height: 100px;
    background: var(--cocoa);
  }
  .brand-name {
    position: absolute; left: 0; right: 0; top: 200px;
    font-family: "Comfortaa", Arial, sans-serif;
    font-weight: 700; font-size: 40px;
    color: var(--sun-yellow); white-space: nowrap;
  }
  .brand-web {
    position: absolute; left: 0; right: 0; top: 308px;
    font-weight: 700; font-size: 15px;
    color: var(--cocoa);
  }
  .brand-web .accent { color: var(--sun-yellow); }
</style>
</head>
<body>

  <section class="card-front">
    <svg class="panel" viewBox="0 0 587 364" width="587" height="364" aria-hidden="true">
      <polygon points="400,0 587,0 587,364 275,364 275,125" fill="var(--cocoa)"/>
    </svg>
    <div class="holder">
      <p class="holder-name">MARCUS ELLERY</p>
      <p class="holder-title">Managing Director</p>
    </div>
    <ul class="contact-list">
      <li>
        <svg viewBox="0 0 24 24"><path d="M6.6 10.8a15.1 15.1 0 0 0 6.6 6.6l2.2-2.2a1 1 0 0 1 1-.25 11.4 11.4 0 0 0 3.6.57 1 1 0 0 1 1 1V20a1 1 0 0 1-1 1A17 17 0 0 1 3 4a1 1 0 0 1 1-1h3.5a1 1 0 0 1 1 1c0 1.25.2 2.45.57 3.57a1 1 0 0 1-.25 1z"/></svg>
        +1 (808) 571 6023
      </li>
      <li>
        <svg viewBox="0 0 24 24"><path d="M2 5h20v14H2z M2 5l10 8 10-8" fill="none" stroke="#fff" stroke-width="2.4"/></svg>
        support@purrnestnookco.com
      </li>
      <li>
        <svg viewBox="0 0 24 24"><circle cx="12" cy="12" r="10"/><path d="M2 12h20M12 2c3 3 3 17 0 20M12 2c-3 3-3 17 0 20" fill="none" stroke="#fdb515" stroke-width="1.5"/></svg>
        www.purrnestnookco.com
      </li>
    </ul>
    <div class="front-mark">
      <span class="front-mark-dot" aria-hidden="true"></span>
      <p class="front-mark-name">Purrnest Nook Co</p>
    </div>
  </section>

  <section class="card-back">
    <span class="brand-square" aria-hidden="true"></span>
    <p class="brand-name">Purrnest Nook Co</p>
    <p class="brand-web">www.<span class="accent">purrnestnookco</span>.com</p>
  </section>

</body>
</html>
```